Business Card for a Dental Office

The design should communicate integrity, quality and reliability. We also want the card look elegant, simple, but still stand out, different from the traditional-dental-office business card.

Industry/Entity Type

Business

```html
<!DOCTYPE html>
<html lang="en">
<head>
<meta charset="utf-8">
<title>Harlow Dental Studio — Business Card</title>
<link rel="stylesheet" href="https://fonts.googleapis.com/css2?family=Arimo:wght@400&display=swap">
<style>
  :root {
    --stage: #2b2b2d;
    --card-black: #0b0b0b;
    --card-white: #ffffff;
    --gold: #c9a22a;
    --ink: #1a1a1a;
    --grey: #8a8a8a;
    --rule: #bdbdbd;
    --white: #f4f4f4;
  }
  * { box-sizing: border-box; margin: 0; padding: 0; }
  html, body { width: 1200px; height: 950px; overflow: hidden; }
  body {
    background: var(--stage);
    font-family: "Arimo", Arial, sans-serif;
    position: relative;
  }
  .card {
    position: absolute;
    left: 220px;
    width: 760px;
    height: 430px;
    border-radius: 4px;
    overflow: hidden;
  }
  .card--front { top: 35px; background: var(--card-black); }
  .card--back { top: 485px; background: var(--card-white); }

  .brand {
    position: absolute;
    display: flex;
    align-items: center;
    gap: 16px;
  }
  .brand__mark {
    width: 44px; height: 44px;
    flex: none;
  }
  .brand__name {
    font-family: "Arimo", Arial, sans-serif;
    font-weight: 400;
    font-size: 34px;
    line-height: 1;
    white-space: nowrap;
  }

  .card--front .brand { left: 170px; top: 170px; }
  .card--front .brand__mark { background: var(--gold); }
  .card--front .brand__name { color: var(--white); }
  .front__web {
    position: absolute;
    left: 0; right: 0; top: 300px;
    text-align: center;
    color: var(--white);
    font-size: 18px;
    letter-spacing: 3px;
  }

  .card--back .brand { left: 110px; top: 100px; }
  .card--back .brand__mark { background: var(--ink); }
  .card--back .brand__name { color: var(--ink); }

  .person {
    position: absolute;
    left: 90px; top: 205px;
    width: 265px;
    text-align: right;
  }
  .holder__name { font-size: 26px; color: var(--ink); }
  .holder__role { font-size: 18px; color: var(--gold); margin-top: 4px; }
  .address {
    margin-top: 40px;
    font-size: 19px; color: var(--grey); line-height: 1.35;
  }

  .divider {
    position: absolute; left: 375px; top: 200px;
    width: 1px; height: 165px; background: var(--rule);
  }

  .contacts {
    position: absolute; left: 400px; top: 192px;
    list-style: none;
  }
  .contacts li {
    display: flex; align-items: center; gap: 12px;
    font-size: 18px; color: var(--grey); height: 31px;
  }
  .contacts svg { width: 18px; height: 18px; fill: var(--ink); flex: none; }
</style>
</head>
<body>

<section class="card card--front" aria-label="Card front">
  <div class="brand">
    <span class="brand__mark"></span>
    <span class="brand__name">Harlow Dental Studio</span>
  </div>
  <p class="front__web">www.harlowdental.com</p>
</section>

<section class="card card--back" aria-label="Card back">
  <div class="brand">
    <span class="brand__mark"></span>
    <span class="brand__name">Harlow Dental Studio</span>
  </div>

  <div class="person">
    <p class="holder__name">Marcus Ellery</p>
    <p class="holder__role">President</p>
    <p class="address">2170 Linden Avenue<br>Maple Grove, NY 11020</p>
  </div>

  <span class="divider"></span>

  <ul class="contacts">
    <li>
      <svg viewBox="0 0 20 20" aria-hidden="true"><path d="M2 7c0-3 3-4 8-4s8 1 8 4v2h-4V7H6v2H2zM5 10h10l2 7H3z"/></svg>
      555 0142 7781
    </li>
    <li>
      <svg viewBox="0 0 20 20" aria-hidden="true"><path d="M6 1h8a1 1 0 0 1 1 1v16a1 1 0 0 1-1 1H6a1 1 0 0 1-1-1V2a1 1 0 0 1 1-1zm1 2v12h6V3zm3 13a1 1 0 1 0 0 2 1 1 0 0 0 0-2z"/></svg>
      555 0198 3364
    </li>
    <li>
      <svg viewBox="0 0 20 20" aria-hidden="true"><path d="M5 2h8l2 2v4H5zM2 9h16v7h-3v3H5v-3H2zm5 5v3h6v-3z"/></svg>
      555 0177 2049
    </li>
    <li>
      <svg viewBox="0 0 20 20" aria-hidden="true"><path d="M2 4h16v12H2zm1.5 1.5 6.5 5 6.5-5z"/></svg>
      marcus@harlowdental.com
    </li>
    <li>
      <svg viewBox="0 0 20 20" aria-hidden="true"><path d="M10 1a9 9 0 1 0 0 18 9 9 0 0 0 0-18zm0 2c1 1 2 3 2.3 6H7.7C8 6 9 4 10 3zM3 11h3c.1 2 .6 4 1.5 5.5A7 7 0 0 1 3 11zm4.7 0h4.6c-.2 2.5-1.2 4.5-2.3 6-1.1-1.5-2.1-3.5-2.3-6zM14 11h3a7 7 0 0 1-4.5 5.5c.9-1.5 1.4-3.5 1.5-5.5z"/></svg>
      www.harlowdental.com
    </li>
  </ul>
</section>

</body>
</html>
```